Harbor Loom Floors Letterhead

Letterhead used for business reasons. It must be editable and easy to use.

Address is 2715 W. Pelican Lane Marlow Bay CA 34187 - 941.382.6519

```html
<!DOCTYPE html>
<html lang="en">
<head>
<meta charset="utf-8">
<title>Harbor Loom Floors Letterhead</title>
<link href="https://fonts.googleapis.com/css2?family=Lato:wght@400;700&family=Montserrat:wght@400&family=Parisienne&display=swap" rel="stylesheet">
<style>
  :root {
    --backdrop: #e4e4e4;
    --paper: #ffffff;
    --accent: #e08a2a;
    --ink: #1f1f1f;
    --ink-soft: #3a3a3a;
  }
  * { box-sizing: border-box; margin: 0; padding: 0; }
  html, body {
    width: 1174px; height: 1200px; overflow: hidden;
    background: var(--backdrop);
  }
  .letterhead {
    position: absolute; left: 146px; top: 30px;
    width: 881px; height: 1140px;
    background: var(--paper);
    box-shadow: 0 2px 8px rgba(0,0,0,0.15);
    font-family: "Lato", sans-serif;
    color: var(--ink);
  }
  .brand {
    position: absolute; left: 56px; top: 50px;
    font-family: "Lato", sans-serif; font-weight: 400;
    font-size: 30px; line-height: 36px;
    color: var(--accent);
    display: flex; align-items: center; gap: 10px;
  }
  .brand-dot {
    width: 14px; height: 14px; border-radius: 50%;
    background: var(--accent);
  }
  .contact {
    position: absolute; left: 634px; top: 87px;
    height: 63px; padding-left: 26px;
    border-left: 2px solid var(--accent);
    font-family: "Montserrat", sans-serif;
    font-size: 15.5px; line-height: 20px;
    color: var(--ink-soft);
  }
  .contact .phone {
    margin-top: 10px; display: flex; align-items: center; gap: 5px;
  }
  .contact svg { width: 12px; height: 12px; }
  .block { position: absolute; left: 56px; font-size: 17.5px; line-height: 20px; }
  .date { top: 280px; }
  .recipient { top: 322px; }
  .company { top: 399px; }
  .salutation { top: 500px; font-size: 21px; font-weight: 700; }
  .body-copy {
    position: absolute; left: 56px; top: 564px; width: 771px;
    font-size: 17.1px; line-height: 19px; text-align: justify;
  }
  .body-copy p { margin-bottom: 18px; }
  .closing { top: 910px; }
  .signature {
    position: absolute; left: 56px; top: 990px;
    font-family: "Parisienne", cursive; font-size: 38px; color: #111;
  }
</style>
</head>
<body>
  <div class="letterhead">
    <div class="brand"><span class="brand-dot"></span>Harbor Loom Floors</div>

    <div class="contact">
      <div>2715 W. Pelican Lane</div>
      <div>Marlow Bay CA 34187</div>
      <div class="phone">
        <svg viewBox="0 0 24 24" aria-hidden="true"><path fill="#e08a2a" d="M6.6 10.8a15.1 15.1 0 0 0 6.6 6.6l2.2-2.2a1 1 0 0 1 1-.25 11.4 11.4 0 0 0 3.6.57 1 1 0 0 1 1 1V20a1 1 0 0 1-1 1A17 17 0 0 1 3 4a1 1 0 0 1 1-1h3.5a1 1 0 0 1 1 1c0 1.25.2 2.45.57 3.57a1 1 0 0 1-.25 1z"/></svg>
        <span>555.382.6519</span>
      </div>
    </div>

    <div class="block date">January-03-2020</div>
    <div class="block recipient">Mr, Daniel Reyes<br>President</div>
    <div class="block company">Crestline Partners<br>123 Street Name, Suite# 10<br>City, State, 120023</div>
    <div class="block salutation">Dear Mr, Daniel</div>

    <div class="body-copy">
      <p>Lorem ipsum dolor sit amet, consectetur adipiscing elit, sed do eiusmod tempor incididunt ut labore et dolore magna aliqua. Ut enim ad minim veniam, quis nostrud exercitation ullamco laboris nisi ut aliquip ex ea commodo consequat. Duis aute irure dolor in reprehenderit in voluptate velit esse cillum dolore eu fugiat nulla pariatur.</p>
      <p>Lorem ipsum dolor sit amet, consectetur adipiscing elit, sed do eiusmod tempor incididunt ut labore et dolore magna aliqua. Ut enim ad minim veniam, quis nostrud exercitation ullamco laboris nisi ut aliquip ex ea commodo consequat. Duis aute irure dolor in reprehenderit in voluptate velit esse cillum dolore eu fugiat nulla pariatur.</p>
      <p>Lorem ipsum dolor sit amet, consectetur adipiscing elit, sed do eiusmod tempor incididunt ut labore et dolore magna aliqua. Ut enim ad minim veniam, quis nostrud exercitation ullamco laboris nisi ut aliquip ex ea commodo consequat.</p>
      <p>Excepteur sint occaecat cupidatat non proident, sunt in culpa qui officia deserunt mollit anim id est laborum. re et dolore magnam aliquam quaerat voluptatem.</p>
    </div>

    <div class="block closing">Regards</div>
    <div class="signature">Laura Bennett</div>
  </div>
</body>
</html>
```